Education Certificate

We need a modern yet professional Certificate for those who successfully pass / complete our online Training course.

There are various courses but ONE certificate design required.

the certificate needs to look extremely professional and of value.

```html
<!DOCTYPE html>
<html lang="en">
<head>
<meta charset="UTF-8">
<title>Certificate of Completion</title>
<link rel="stylesheet" href="https://fonts.googleapis.com/css2?family=Poppins:wght@400;500;600;800&family=Great+Vibes&family=Cinzel:wght@600&display=swap">
<style>
  :root {
    --page-bg: #d8d9e3;
    --navy: #1f2f6e;
    --ink: #17171c;
    --paper: #ffffff;
    --paper-shade: #eef0f3;
    --gold-light: #f3d36a;
    --gold: #d4a72c;
    --gold-dark: #9c7416;
  }
  * { margin: 0; padding: 0; box-sizing: border-box; }
  html, body {
    width: 834px; height: 1200px; overflow: hidden;
    background: var(--page-bg);
  }
  .canvas { position: relative; width: 834px; height: 1200px; }
  .certificate {
    position: absolute; left: 37px; top: 306px;
    width: 760px; height: 587px;
    background: var(--navy);
    box-shadow: 0 4px 14px rgba(20, 25, 60, 0.18);
  }
  .gold-corner {
    position: absolute;
    background: linear-gradient(160deg, var(--gold-dark), var(--gold-light) 45%, var(--gold) 70%, var(--gold-dark));
  }
  .gold-corner--top { left: 504px; top: 32px; width: 222px; height: 205px; }
  .gold-corner--bottom { left: 36px; top: 347px; width: 221px; height: 207px; }
  .sheet {
    position: absolute; left: 44px; top: 40px; width: 672px; height: 507px;
    background: linear-gradient(135deg, var(--paper) 0%, var(--paper-shade) 40%, var(--paper) 70%, var(--paper-shade) 100%);
  }
  .centered { position: absolute; left: 0; width: 760px; text-align: center; white-space: nowrap; }
  .brand {
    top: 72px; display: flex; justify-content: center; align-items: center; gap: 8px;
    font-family: 'Poppins', sans-serif; font-weight: 500; font-size: 10px;
    letter-spacing: 0.4px; color: var(--navy); line-height: 1.2; text-align: left;
  }
  .brand-mark { width: 46px; height: 46px; background: var(--navy); flex: none; }
  .title {
    top: 135px; font-family: 'Poppins', sans-serif; font-weight: 800;
    font-size: 57px; line-height: 1; color: var(--navy); letter-spacing: -0.5px;
  }
  .subtitle {
    top: 199px; font-family: 'Poppins', sans-serif; font-weight: 500;
    font-size: 25px; line-height: 1; letter-spacing: 6px; color: var(--ink);
  }
  .presented {
    top: 243px; font-family: 'Poppins', sans-serif; font-weight: 500;
    font-size: 18px; line-height: 1; letter-spacing: 0.9px; color: var(--ink);
  }
  .recipient {
    top: 294px; font-family: 'Great Vibes', cursive;
    font-size: 64px; line-height: 1; word-spacing: 10px; color: var(--ink);
  }
  .rule { position: absolute; height: 1px; background: var(--navy); }
  .rule--name { left: 180px; top: 348px; width: 399px; }
  .rule--course { left: 180px; top: 421px; width: 399px; }
  .rule--signature { left: 101px; top: 488px; width: 160px; }
  .rule--date { left: 493px; top: 488px; width: 159px; }
  .achievement {
    top: 372px; font-family: 'Poppins', sans-serif; font-weight: 400;
    font-size: 16.5px; line-height: 1; letter-spacing: 0.3px; color: var(--ink);
  }
  .field-label {
    position: absolute; top: 502px; font-family: 'Cinzel', serif; font-weight: 600;
    font-size: 12px; letter-spacing: 0.8px; color: var(--navy); text-align: center;
  }
  .field-label--signature { left: 101px; width: 160px; }
  .field-label--date { left: 493px; width: 159px; }
  .seal {
    position: absolute; left: 333px; top: 435px; width: 94px; height: 94px;
    border-radius: 50%;
    background: radial-gradient(circle at 40% 35%, var(--gold-light), var(--gold) 55%, var(--gold-dark));
  }
</style>
</head>
<body>
<div class="canvas">
  <div class="certificate">
    <div class="gold-corner gold-corner--top"></div>
    <div class="gold-corner gold-corner--bottom"></div>
    <div class="sheet"></div>

    <div class="centered brand">
      <span class="brand-mark"></span>
      <span>GLOBAL SERVICE<br>EXCELLENCE<br>ACADEMY</span>
    </div>

    <h1 class="centered title">CERTIFICATE</h1>
    <p class="centered subtitle">OF COMPLETION</p>
    <p class="centered presented">THIS CERTIFICATE IS PROUDLY PRESENTED TO</p>
    <div class="rule rule--name"></div>
    <p class="centered recipient">Clara Whitfield</p>
    <p class="centered achievement">For successfully completing our online training course.</p>
    <div class="rule rule--course"></div>

    <div class="seal" role="img" aria-label="Gold award seal"></div>

    <div class="rule rule--signature"></div>
    <div class="rule rule--date"></div>
    <p class="field-label field-label--signature">SIGNATURE</p>
    <p class="field-label field-label--date">DATE</p>
  </div>
</div>
</body>
</html>
```